VENTURE CAPITAL GROUP BUSINESS CARD DESIGN

Venture Capital Group based in SF looking for a bold business card design. No trendy colour explosion, 3D effects etc. Just "simple" optical effects. Works on your brain, keeps your eye focused and sticks to your mind.
Target Market(s)
Technology startups
Industry/Entity Type
Venture Capital
Contact Information for Business Card
DESMOND WHITLAKE
MANAGING PARTNER
187 FENWORTH ST SAN FRANCISCO, CA 94187
415.555.0142 O
415.555.0147 F
415.555.0193 C
desmond@veldtmoorcapital.ventures

```html
<!DOCTYPE html>
<html lang="en">
<head>
<meta charset="utf-8">
<title>Veldtmoor Capital Group – Business Card</title>
<link href="https://fonts.googleapis.com/css2?family=Cinzel:wght@400&family=PT+Sans:wght@400;700&display=swap" rel="stylesheet">
<style>
  :root {
    --backdrop: #151515;
    --card-white: #ffffff;
    --brand-green: #1f7a2c;
    --band-light: #4fb84a;
    --band-dark: #1b7a22;
    --back-center: #55b750;
    --back-edge: #0a4a10;
    --ink: #1a1a1a;
    --seal-grey: #ececec;
  }
  * { margin: 0; padding: 0; box-sizing: border-box; }
  html, body {
    width: 1200px; height: 900px; overflow: hidden;
    background: var(--backdrop);
  }
  .canvas { position: relative; width: 1200px; height: 900px; }
  .card {
    position: absolute; top: 170px; width: 347px; height: 561px;
  }
  .card-front { left: 259px; background: var(--card-white); }
  .card-back {
    left: 631px;
    background: radial-gradient(ellipse 70% 55% at 50% 52%, var(--back-center) 0%, #2f8a32 50%, var(--back-edge) 100%);
  }
  .band {
    position: absolute; left: 102px; width: 143px; height: 29px;
    background: linear-gradient(to bottom, var(--band-light), var(--band-dark));
  }
  .band-top { top: 0; }
  .band-bottom { bottom: 0; background: linear-gradient(to top, var(--band-light), var(--band-dark)); }
  .seal {
    position: absolute; border-radius: 50%;
  }
  .card-front .seal { left: 108px; top: 62px; width: 130px; height: 130px; background: var(--seal-grey); }
  .card-back .seal { left: 102px; top: 168px; width: 144px; height: 144px; background: var(--card-white); }
  .brand-name {
    position: absolute; left: 0; width: 100%; text-align: center;
    font-family: "Cinzel", serif; font-weight: 400; font-size: 30px; letter-spacing: 0.5px;
    line-height: 1.1;
  }
  .card-front .brand-name { top: 208px; color: var(--brand-green); }
  .card-back .brand-name { top: 332px; color: var(--card-white); }
  .holder {
    position: absolute; top: 286px; left: 0; width: 100%; text-align: center;
    font-family: "PT Sans", sans-serif;
  }
  .holder-name { font-weight: 700; font-size: 19px; color: var(--brand-green); }
  .holder-title { font-size: 14px; color: var(--ink); margin-top: 2px; }
  .contact {
    position: absolute; top: 382px; left: 0; width: 100%;
    display: flex; flex-direction: column; align-items: center;
    font-family: "PT Sans", sans-serif; font-size: 15px; color: var(--ink);
  }
  .contact-line { display: flex; align-items: center; gap: 6px; height: 23px; }
  .contact-line svg { width: 11px; height: 11px; fill: var(--brand-green); }
  .address { margin-top: 9px; }
</style>
</head>
<body>
<main class="canvas">
  <section class="card card-front" aria-label="Card front">
    <div class="band band-top"></div>
    <div class="seal"></div>
    <div class="brand-name">Veldtmoor Capital Group</div>
    <div class="holder">
      <div class="holder-name">Desmond Whitlake</div>
      <div class="holder-title">Managing Partner</div>
    </div>
    <div class="contact">
      <div class="contact-line">
        <svg viewBox="0 0 12 12" aria-hidden="true"><path d="M2.5 0.5l2 2.4-1 1.3c.7 1.5 1.8 2.6 3.3 3.3l1.3-1 2.4 2-1.2 2c-4.5-.3-8.1-3.9-8.4-8.4z"/></svg>
        <span>415.555.0142</span>
      </div>
      <div class="contact-line">
        <svg viewBox="0 0 12 12" aria-hidden="true"><path d="M3 0h5l1 1v3H3zM1 5h10v6H1zm2 2v1h2V7zm4 0v1h2V7z"/></svg>
        <span>415.555.0147</span>
      </div>
      <div class="contact-line">
        <svg viewBox="0 0 12 12" aria-hidden="true"><path d="M3 0h6v12H3zm1 1.5v7.5h4V1.5zM5.5 10h1v1h-1z" fill-rule="evenodd"/></svg>
        <span>415.555.0193</span>
      </div>
      <div class="contact-line">
        <svg viewBox="0 0 12 12" aria-hidden="true"><path d="M0 2h12v1L6 7 0 3zm0 2.5l6 4 6-4V10H0z"/></svg>
        <span>desmond@veldtmoorcapital.ventures</span>
      </div>
      <div class="address">187 Fenworth St San Francisco, CA 94187</div>
    </div>
    <div class="band band-bottom"></div>
  </section>

  <section class="card card-back" aria-label="Card back">
    <div class="seal"></div>
    <div class="brand-name">Veldtmoor Capital Group</div>
  </section>
</main>
</body>
</html>
```